Corvane Capital Business Cards

These are professional business cards that are for my family office.
Put fake emails and phone numbers as of now until I finalize those components. This family office controls my families investments, assets, and future. The cards should be professional.
..
.
.
.
I just uploaded another variation of a logo I would like to see as a business card to I am inbeteen which logo to use

Target Market(s)

business

Industry/Entity Type

business

Contact Information for Business Card

Professional, wealth related, finance related.

Requirements
Must have
• Logo

```html
<!DOCTYPE html>
<html lang="en">
<head>
<meta charset="utf-8">
<title>Corvane Capital Business Cards</title>
<link href="https://fonts.googleapis.com/css2?family=Montserrat:wght@400;500;600;700&display=swap" rel="stylesheet">
<style>
  :root {
    --navy: #1a1f2e;
    --navy-deep: #161b29;
    --navy-soft: #2a3146;
    --ink: #1c2130;
    --text-grey: #3a3d45;
    --paper: #ffffff;
    --backdrop: #3b3c3e;
  }
  * { margin: 0; padding: 0; box-sizing: border-box; }
  html, body {
    width: 1200px;
    height: 1059px;
    overflow: hidden;
    background: var(--backdrop);
    font-family: "Montserrat", sans-serif;
  }
  .canvas { position: relative; width: 1200px; height: 1059px; }

  .card {
    position: absolute;
    left: 256px;
    width: 688px;
    height: 393px;
    border-radius: 24px;
    overflow: hidden;
  }

  /* Front */
  .card-front { top: 100px; background: var(--paper); color: var(--ink); }
  .wordmark {
    position: absolute;
    left: 30px;
    top: 44px;
    font-size: 31px;
    font-weight: 600;
    letter-spacing: 1px;
    text-transform: uppercase;
    color: var(--ink);
  }
  .brand-block {
    position: absolute;
    left: 474px;
    top: 25px;
    width: 190px;
    text-align: center;
  }
  .brand-ring {
    display: block;
    width: 108px;
    height: 108px;
    margin: 0 auto;
    border: 3px solid var(--ink);
    border-radius: 50%;
  }
  .brand-name {
    margin-top: 13px;
    font-size: 17px;
    font-weight: 600;
    letter-spacing: 0.5px;
    text-transform: uppercase;
    color: var(--ink);
  }
  .accent-bar {
    position: absolute;
    left: 0;
    top: 200px;
    width: 20px;
    height: 56px;
    background: var(--navy);
  }
  .person-name {
    position: absolute;
    left: 30px;
    top: 196px;
    font-size: 30px;
    font-weight: 700;
    letter-spacing: 0.3px;
    color: var(--ink);
  }
  .person-title {
    position: absolute;
    left: 30px;
    top: 235px;
    font-size: 18px;
    font-weight: 400;
    color: var(--text-grey);
  }
  .divider {
    position: absolute;
    left: 30px;
    top: 274px;
    width: 633px;
    height: 2px;
    background: var(--ink);
  }
  .contact-list {
    position: absolute;
    left: 30px;
    top: 290px;
    list-style: none;
  }
  .contact-item {
    display: flex;
    align-items: center;
    height: 27px;
    font-size: 18px;
    color: var(--text-grey);
  }
  .contact-icon { width: 14px; height: 14px; margin-right: 9px; fill: var(--ink); }
  .address {
    position: absolute;
    right: 25px;
    top: 320px;
    text-align: right;
    font-size: 18px;
    line-height: 27px;
    color: var(--text-grey);
  }

  /* Back */
  .card-back { top: 536px; background: var(--navy); }
  .back-texture {
    position: absolute;
    inset: 0;
    background: linear-gradient(120deg, var(--navy-deep) 0%, var(--navy) 50%, var(--navy-soft) 100%);
  }
  .back-brand {
    position: absolute;
    left: 0;
    right: 0;
    top: 198px;
    text-align: center;
  }
  .back-ring {
    display: block;
    width: 62px;
    height: 62px;
    margin: 0 auto;
    border: 2.5px solid var(--paper);
    border-radius: 50%;
  }
  .back-name {
    margin-top: 9px;
    font-size: 13px;
    font-weight: 600;
    letter-spacing: 0.6px;
    text-transform: uppercase;
    color: var(--paper);
  }
</style>
</head>
<body>
<main class="canvas">

  <section class="card card-front">
    <div class="wordmark">Corvane Capital</div>

    <div class="brand-block">
      <span class="brand-ring"></span>
      <div class="brand-name">Corvane Capital</div>
    </div>

    <div class="accent-bar"></div>
    <h1 class="person-name">ELLIOT MARSH</h1>
    <p class="person-title">Managing Director</p>
    <div class="divider"></div>

    <ul class="contact-list">
      <li class="contact-item">
        <svg class="contact-icon" viewBox="0 0 16 16" aria-hidden="true"><path d="M1 6c0-2 3-3.5 7-3.5S15 4 15 6v1.2h-3.3V5.6c-1-.4-2.3-.6-3.7-.6s-2.7.2-3.7.6v1.6H1zM4 8.2 5.5 6.5h5L12 8.2 13.5 14h-11z"/></svg>
        123 456 789
      </li>
      <li class="contact-item">
        <svg class="contact-icon" viewBox="0 0 16 16" aria-hidden="true"><path d="M1 3.5h14v1.2L8 9 1 4.7zM1 6.3l7 4.3 7-4.3v6.2H1z"/></svg>
        info@yourgmail.com
      </li>
      <li class="contact-item">
        <svg class="contact-icon" viewBox="0 0 16 16" aria-hidden="true"><path d="M8 1a7 7 0 1 0 0 14A7 7 0 0 0 8 1zm-1 2.3c-.6.8-1.5 1-1.9 1.8-.3.6.2 1.3.9 1.4.8.1 1.4.7 1.2 1.5-.2.9-1.2 1.3-1.2 2.3 0 .8.5 1.5.4 2.3A5.6 5.6 0 0 1 7 3.3zm2.5 9.5c.2-.9.9-1.5 1.5-2.2.5-.7.3-1.6-.5-1.9-.7-.3-1.5-.4-1.6-1.2-.1-.7.7-1 1.2-1.4.4-.3.3-.9.1-1.3a5.6 5.6 0 0 1-.7 8z"/></svg>
        www.yourwebsite.com
      </li>
    </ul>

    <address class="address" style="font-style: normal;">
      Your address, City<br>
      State, Zip 1234
    </address>
  </section>

  <section class="card card-back">
    <div class="back-texture" role="img" aria-label="Embossed tonal pattern of repeated brand marks on dark navy"></div>
    <div class="back-brand">
      <span class="back-ring"></span>
      <div class="back-name">Corvane Capital</div>
    </div>
  </section>

</main>
</body>
</html>
```